Counseling Practice Business Card

I need a professional looking business card incorporating my new logo that was just completed. Card needs to incorporate my name and title, description of my specialty, my address, my phone number, my fax number, my email and my website URL. I need to be able to choose design on/with different paper colors and textures.
I do not have a lot of business card ideas so I am open to anything but I want bold,sharp, clear card without additional designs other than my logo (see attached file info). I am open to different color backgrounds or paper colors including black. I do not like traditional brackets around area codes in phone number or dashes between numbers in phone number. Am open to other ways of presenting including periods between numbers as appropriate. I do not know enough to know what I like yet but I want card to coordinate and work together with my logo. My practice emphasizes natural mental health interventions so any use of color (with background paper color or the blue and green in my logo) that elicits nature is nice. In addition to black, any natural brown or wood looking background might be desirable also. Most of the offerings so far look very similar and boring.

Target Market(s)

Potential therapy clients and other professionals

Contact Information for Business Card

Card information:
Gerald M. Whitcombe, Ph.D.
Licensed Clinical Psychologist
Integrative Health Coach
4812 Marlowe Ridge Blvd SE
Suite 310
Duluth, GA 30096
(770) 415-2983 phone
(770) 581-4096 fax
drgeraldwhitcombe@quillmarsh.net
brightfernwellness.net

Font styles to use
Serif
Sans Serif
Other font styles liked:
• anything that you think looks crisp, clear and easily readable

Requirements
Must have
• Any color used should coordinate with my logo design (see attached files).
• Card should be printed horizontally so top and bottom are longest sides of rectangle.
• Background color or paper color should complement and highlight logo. Do not like a white background. black, grey, brown or any color my logo would blend well with.
Nice to have
• I would like designer to utilize color to highlight letters/name or phone-fax-web symbols.
• Bottom edge of card could be highlighted if appropriate to an idea.
Should not have
• I would NOT want the card to have a pure white background at all.
• No clear cards.
• Cards should be oriented with long sides on bottom and top, NOT sides. DO NOT LIKE THIS THIN TALL ORIENTATION.

```html
<!DOCTYPE html>
<html lang="en">
<head>
<meta charset="utf-8">
<title>Brightfern Wellness – Business Card</title>
<link rel="stylesheet" href="https://fonts.googleapis.com/css2?family=Roboto:wght@400;500&family=Roboto+Condensed:wght@400;700&display=swap">
<style>
  :root {
    --backdrop: #3a3a3c;
    --card: #1d1f21;
    --brand-blue: #2a8fd6;
    --sky-blue: #3aa7e3;
    --leaf-green: #1e8a3c;
    --text-light: #eef0f2;
    --divider: #8a8c8f;
  }
  * { margin: 0; padding: 0; box-sizing: border-box; }
  html, body {
    width: 1200px; height: 900px; overflow: hidden;
    background: var(--backdrop);
  }
  .canvas {
    position: relative; width: 1200px; height: 900px;
    display: flex; flex-direction: column; align-items: center; justify-content: center;
    gap: 40px;
  }
  .card {
    position: relative; width: 660px; height: 377px;
    background: var(--card);
    box-shadow: 0 6px 18px rgba(0,0,0,0.45);
  }

  /* Front */
  .card-front {
    display: flex; flex-direction: column; align-items: center; justify-content: center;
  }
  .brand-name {
    font-family: "Roboto", sans-serif; font-weight: 500;
    font-size: 50px; color: var(--sky-blue); letter-spacing: 1px;
  }
  .front-url {
    margin-top: 44px;
    font-family: "Roboto", sans-serif; font-size: 15px;
    letter-spacing: 5px; color: var(--text-light);
  }

  /* Back */
  .card-back { padding: 0 40px; }
  .identity {
    position: absolute; right: 355px; top: 120px; text-align: right;
  }
  .person-name {
    font-family: "Roboto Condensed", sans-serif; font-weight: 700;
    font-size: 22px; color: var(--brand-blue); line-height: 1.1;
  }
  .person-title {
    font-family: "Roboto Condensed", sans-serif; font-weight: 400;
    font-size: 17px; color: var(--leaf-green); line-height: 1.25;
  }
  .divider {
    position: absolute; left: 325px; top: 124px; width: 1px; height: 100px;
    background: var(--divider);
  }
  .contact-list {
    position: absolute; left: 345px; top: 132px; list-style: none;
    font-family: "Roboto", sans-serif; font-size: 16px; color: var(--text-light);
  }
  .contact-list li { display: flex; align-items: center; gap: 10px; height: 21px; }
  .contact-list svg { width: 14px; height: 14px; fill: var(--brand-blue); flex: none; }
  .address {
    position: absolute; left: 130px; bottom: 60px;
    display: flex; align-items: center; gap: 8px;
    font-family: "Roboto", sans-serif; font-size: 17px; color: var(--text-light);
  }
  .address svg { width: 14px; height: 18px; fill: var(--brand-blue); }
</style>
</head>
<body>
<main class="canvas">
  <section class="card card-front">
    <div class="brand-name">Brightfern Wellness</div>
    <div class="front-url">www.brightfernwellness.net</div>
  </section>

  <section class="card card-back">
    <div class="identity">
      <div class="person-name">GERALD M. WHITCOMBE, PH.D.</div>
      <div class="person-title">Licensed Clinical Psychologist</div>
      <div class="person-title">Integrative Health Coach</div>
    </div>
    <div class="divider"></div>
    <ul class="contact-list">
      <li>
        <svg viewBox="0 0 24 24" aria-hidden="true"><path d="M6.6 10.8a15.2 15.2 0 0 0 6.6 6.6l2.2-2.2c.3-.3.7-.4 1-.2 1.1.4 2.3.6 3.6.6.6 0 1 .4 1 1V20c0 .6-.4 1-1 1A17 17 0 0 1 3 4c0-.6.4-1 1-1h3.5c.6 0 1 .4 1 1 0 1.3.2 2.5.6 3.6.1.3 0 .7-.2 1z"/></svg>
        <span class="contact-phone">(770) 415-2983</span>
      </li>
      <li>
        <svg viewBox="0 0 24 24" aria-hidden="true"><path d="M7 3h10v5H7zM4 9h16a2 2 0 0 1 2 2v6h-4v4H6v-4H2v-6a2 2 0 0 1 2-2zm4 7v3h8v-3z"/></svg>
        <span class="contact-fax">(770) 581-4096</span>
      </li>
      <li>
        <svg viewBox="0 0 24 24" aria-hidden="true"><path d="M2 5h20v14H2zm2 2v.5l8 5 8-5V7l-8 5z"/></svg>
        <span class="contact-email">drgeraldwhitcombe@quillmarsh.net</span>
      </li>
      <li>
        <svg viewBox="0 0 24 24" aria-hidden="true"><circle cx="12" cy="12" r="10"/><path d="M2 12h20M12 2c3 3 3 17 0 20M12 2c-3 3-3 17 0 20" stroke="#1d1f21" stroke-width="1.4" fill="none"/></svg>
        <span class="contact-web">www.brightfernwellness.net</span>
      </li>
    </ul>
    <div class="address">
      <svg viewBox="0 0 14 20" aria-hidden="true"><path d="M7 0a7 7 0 0 0-7 7c0 5 7 13 7 13s7-8 7-13a7 7 0 0 0-7-7zm0 9.5A2.5 2.5 0 1 1 7 4.5a2.5 2.5 0 0 1 0 5z"/></svg>
      <span>4812 Marlowe Ridge Blvd SE, Suite 310, Duluth, GA 30096</span>
    </div>
  </section>
</main>
</body>
</html>
```